FunBrixo Business Card

We need a business card design for our company. We sell construction-themed amusement rides for kids.

Contact Information for Business Card

Contact info on business card should include:
Carl Dunning
Co-Founder & COO
(833) 571-FUNBRIX
Carl@funbrixo-demo.com
www.funbrixo-demo.com

```html
<!DOCTYPE html>
<html lang="en">
<head>
<meta charset="utf-8">
<title>FunBrixo Business Card</title>
<link href="https://fonts.googleapis.com/css2?family=Poppins:wght@400;600;700;800&display=swap" rel="stylesheet">
<style>
  :root {
    --stage: #8f8f8f;
    --card-dark: #1d1e20;
    --card-light: #f6f6f7;
    --orange: #ef7424;
    --purple: #8a2a92;
    --blue: #1ea7e1;
    --pink: #e6157f;
    --yellow: #f3a51d;
    --text-grey: #4a4a4a;
  }
  * { box-sizing: border-box; margin: 0; padding: 0; }
  html, body { width: 1200px; height: 960px; overflow: hidden; }
  body {
    background: var(--stage);
    font-family: "Poppins", sans-serif;
    position: relative;
  }
  .card {
    position: absolute;
    width: 700px;
    height: 400px;
    border-radius: 26px;
    overflow: hidden;
  }
  .card--front {
    left: 80px; top: 60px;
    background: var(--card-dark);
    display: flex; align-items: center; justify-content: center; gap: 22px;
  }
  .brand-dot {
    width: 54px; height: 54px; border-radius: 50%;
    background: var(--orange);
  }
  .brand-name--front {
    font-weight: 800; font-size: 92px; line-height: 1;
    color: var(--orange); letter-spacing: -1px;
  }
  .card--back {
    left: 420px; top: 500px;
    background: var(--card-light);
  }
  .back-logo {
    position: absolute; left: 70px; top: 150px;
    display: flex; align-items: center; gap: 12px;
  }
  .brand-dot--small { width: 30px; height: 30px; border-radius: 50%; background: var(--purple); }
  .brand-name--back { font-weight: 800; font-size: 46px; color: var(--purple); line-height: 1; }
  .divider {
    position: absolute; left: 372px; top: 120px;
    width: 1.5px; height: 150px; background: var(--orange);
  }
  .contact { position: absolute; left: 400px; top: 122px; }
  .contact__name { font-weight: 700; font-size: 24px; color: var(--orange); letter-spacing: 0.5px; }
  .contact__title { font-size: 16px; color: var(--blue); margin-top: -2px; }
  .contact__list { list-style: none; margin-top: 22px; }
  .contact__list li {
    display: flex; align-items: center; gap: 8px;
    font-size: 15px; color: var(--text-grey); line-height: 1.45;
  }
  .contact__list svg { width: 12px; height: 12px; fill: var(--orange); flex: none; }
  .color-band { position: absolute; left: 0; right: 0; bottom: 0; height: 9px; display: flex; }
  .color-band span { flex: 1; }
</style>
</head>
<body>
  <section class="card card--front" aria-label="Card front">
    <div class="brand-dot"></div>
    <div class="brand-name--front">FunBrixo</div>
  </section>

  <section class="card card--back" aria-label="Card back">
    <div class="back-logo">
      <div class="brand-dot--small"></div>
      <div class="brand-name--back">FunBrixo</div>
    </div>
    <div class="divider"></div>
    <div class="contact">
      <div class="contact__name">CARL DUNNING</div>
      <div class="contact__title">Co-Founder &amp; COO</div>
      <ul class="contact__list">
        <li><svg viewBox="0 0 24 24"><path d="M6.6 10.8a15 15 0 0 0 6.6 6.6l2.2-2.2c.3-.3.7-.4 1-.2 1.1.4 2.3.6 3.6.6.6 0 1 .4 1 1V20c0 .6-.4 1-1 1A17 17 0 0 1 3 4c0-.6.4-1 1-1h3.5c.6 0 1 .4 1 1 0 1.3.2 2.5.6 3.6.1.3 0 .7-.2 1z"/></svg>(833) 571-FUNBRIX</li>
        <li><svg viewBox="0 0 24 24"><path d="M2 5h20v14H2zm2 2v.5l8 5 8-5V7l-8 5z"/></svg>Carl@funbrixo-demo.com</li>
        <li><svg viewBox="0 0 24 24"><circle cx="12" cy="12" r="10"/></svg>www.funbrixo-demo.com</li>
      </ul>
    </div>
    <div class="color-band">
      <span style="background:var(--orange)"></span>
      <span style="background:var(--purple)"></span>
      <span style="background:var(--blue)"></span>
      <span style="background:var(--pink)"></span>
      <span style="background:var(--yellow)"></span>
    </div>
  </section>
</body>
</html>
```